Linden Medical - Flyer

We are a full service pharmacy that specializes in diabetic testing and medications. We research the patient's insurance to maximize their insurance benefit and then deliver the medications monthly directly to the patient's doorstep, for free! We save the patient, time and money every month.
We would love a flyer that we can distribute to Doctor's offices and patients that sum up our pharmacy. Emphasis on saving money, time, and getting the best quality supplies by maximizing their insurance. We want it to be eye catching, clean, and professional.
You can use our logo or feel free to make your own design.
diabetic patients wanting to save money
Insurance

```html
<!DOCTYPE html>
<html lang="en">
<head>
<meta charset="utf-8">
<title>Linden Medical – Flyer</title>
<link rel="stylesheet" href="https://fonts.googleapis.com/css2?family=Arimo:wght@400;700&display=swap">
<style>
  :root {
    --stage: #e9ecee;
    --sky-top: #c9ecf5;
    --sky-mid: #eaf7fb;
    --paper: #ffffff;
    --leaf: #7bbf2a;
    --leaf-dark: #5a9a1a;
    --headline-green: #6aa51f;
    --ink: #1b1b1b;
    --alert-red: #d21414;
    --teal: #16535f;
    --teal-light: #1f6e7c;
    --white: #ffffff;
  }
  * { box-sizing: border-box; margin: 0; padding: 0; }
  html, body { width: 1200px; height: 1019px; overflow: hidden; }
  body { background: var(--stage); font-family: "Arimo", Arial, sans-serif; color: var(--ink); position: relative; }

  .flyer { position: absolute; top: 179px; width: 532px; height: 687px; overflow: hidden;
    background: radial-gradient(ellipse at 50% 45%, var(--sky-mid) 0%, var(--sky-top) 70%, #b8e2ee 100%); }
  .flyer--front { left: 57px; }
  .flyer--back { left: 613px; width: 527px; }
  .flyer > * { position: absolute; }

  .wave { left: 0; top: 0; width: 100%; height: 100%; }

  .brand { display: flex; align-items: center; gap: 10px; font-weight: 700; color: var(--leaf-dark); white-space: nowrap; }
  .brand__dot { width: 30px; height: 30px; border-radius: 50%; background: var(--leaf); flex: none; }
  .flyer--front .brand { left: 0; width: 100%; top: 30px; justify-content: center; font-size: 34px; }
  .flyer--front .brand__dot { width: 40px; height: 40px; }

  .headline { left: 0; width: 100%; text-align: center; font-weight: 700; text-transform: uppercase; }
  .headline--lead { top: 118px; font-size: 19px; }
  .headline--accent { top: 144px; font-size: 29px; color: var(--headline-green); }
  .headline--tail { top: 180px; font-size: 19px; }

  .benefit { display: flex; align-items: center; gap: 18px; font-size: 20px; line-height: 1.2; text-transform: uppercase; }
  .benefit__icon { width: 68px; height: 68px; border-radius: 50%; background: radial-gradient(circle, #e8c27a 0 40%, var(--leaf) 42%); flex: none; }
  .benefit--meter { left: 73px; top: 240px; }
  .benefit--money { left: 283px; top: 240px; }
  .benefit--time { left: 73px; top: 334px; }
  .benefit--delivery { left: 283px; top: 334px; }

  .finger-art { left: 119px; top: 444px; width: 221px; height: 170px; border-radius: 60px 60px 10px 10px;
    background: linear-gradient(180deg, #f0c3a8, #dc9e84); }

  .gift-bubble { left: 342px; top: 428px; width: 166px; height: 166px; border-radius: 50%;
    background: radial-gradient(circle at 50% 35%, #ffffff 55%, #cfeaf3 100%); text-align: center; padding-top: 20px; }
  .gift-bubble__amount { font-size: 38px; font-weight: 700; display: block; }
  .gift-bubble__text { font-size: 17px; line-height: 1.25; display: block; color: #333; }

  .contact { left: 0; width: 100%; text-align: center; color: var(--white); font-weight: 700; }
  .flyer--front .contact--phone { top: 624px; font-size: 17px; }
  .flyer--front .contact--phone strong { font-size: 26px; }
  .flyer--front .contact--web { top: 656px; font-size: 18px; font-weight: 400; }

  .story { left: 26px; top: 22px; width: 470px; font-size: 17.5px; line-height: 23px; }
  .story p { margin-bottom: 22px; }
  .cta { left: 26px; top: 296px; }
  .cta__title { font-size: 27px; font-weight: 700; color: var(--alert-red); }
  .cta__text { font-size: 17px; line-height: 22px; }

  .ribbon { right: 0; top: 337px; width: 290px; height: 150px; }
  .ribbon__text { position: absolute; color: var(--white); text-align: center; }
  .ribbon__amount { right: 0; top: 6px; width: 115px; font-size: 31px; font-weight: 700; }
  .ribbon__line1 { right: 0; top: 58px; width: 220px; font-size: 23px; }
  .ribbon__line2 { right: 0; top: 103px; width: 200px; font-size: 23px; }

  .figure-art { left: 70px; top: 375px; width: 160px; height: 235px;
    background: linear-gradient(180deg, #3a3a3a, #1f1f1f); border-radius: 40px 40px 6px 6px; opacity: .9; }
  .heart-art { left: 10px; top: 563px; width: 76px; height: 80px; border-radius: 50%;
    background: radial-gradient(circle at 45% 35%, #f04040, #c01616 60%, var(--leaf) 62%); }

  .flyer--back .brand { left: 292px; top: 516px; font-size: 26px; gap: 8px; }
  .flyer--back .contact--web { left: 262px; width: 240px; top: 554px; font-size: 17px; font-weight: 400; color: var(--teal); }
  .flyer--back .contact--phone { top: 640px; left: 20px; font-size: 27px; }
</style>
</head>
<body>

<section class="flyer flyer--front" aria-label="Flyer front side">
  <svg class="wave" viewBox="0 0 532 687" preserveAspectRatio="none" aria-hidden="true">
    <path d="M0 590 C150 625 330 610 532 470 L532 687 L0 687 Z" fill="var(--leaf)"/>
    <path d="M0 580 C150 615 330 600 532 460 L532 470 C330 610 150 625 0 590 Z" fill="#ffffff" opacity=".8"/>
  </svg>

  <div class="brand"><span class="brand__dot"></span>Linden Medical</div>

  <h1 class="headline headline--lead">Are the costs of your</h1>
  <p class="headline headline--accent">Diabetic Testings</p>
  <p class="headline headline--tail">upplies as high as your blood sugar?</p>

  <div class="benefit benefit--meter"><span class="benefit__icon" role="img" aria-label="Compass icon"></span>Free<br>Meter</div>
  <div class="benefit benefit--money"><span class="benefit__icon" role="img" aria-label="Wallet icon"></span>Save<br>Money</div>
  <div class="benefit benefit--time"><span class="benefit__icon" role="img" aria-label="Alarm clock icon"></span>Save<br>Time</div>
  <div class="benefit benefit--delivery"><span class="benefit__icon" role="img" aria-label="Suitcase icon"></span>Free<br>Delivery</div>

  <div class="finger-art" role="img" aria-label="Photo of four fingers with drawn cartoon family faces"></div>

  <div class="gift-bubble">
    <span class="gift-bubble__amount">$20</span>
    <span class="gift-bubble__text">Gift Card<br>is given your<br>first order</span>
  </div>

  <p class="contact contact--phone">Toll Free Number <strong>55510247</strong></p>
  <p class="contact contact--web">www.lindenmedical.com</p>
</section>

<section class="flyer flyer--back" aria-label="Flyer back side">
  <svg class="wave" viewBox="0 0 527 687" preserveAspectRatio="none" aria-hidden="true">
    <path d="M0 430 C90 490 180 560 300 618 L0 687 Z" fill="var(--leaf)" opacity=".35"/>
    <path d="M0 615 C180 650 380 640 527 605 L527 687 L0 687 Z" fill="var(--leaf)"/>
    <path d="M0 605 C180 640 380 630 527 595 L527 605 C380 640 180 650 0 615 Z" fill="#ffffff"/>
  </svg>

  <div class="story">
    <p>We are a full service pharmacy that specializes in diabetic testing supplies and oral medications.</p>
    <p>We research your insurance to determine how to save you the most money</p>
    <p>We then contact your physician to get the appropriate authorization</p>
    <p>We ship your testing supplies and oral medications directly to your home for free!</p>
  </div>

  <div class="cta">
    <p class="cta__title">Get started Today!</p>
    <p class="cta__text">Call our toll free number OR<br>go to our website and fill our form.</p>
  </div>

  <div class="figure-art" role="img" aria-label="Illustration of a businessman with arms raised"></div>

  <div class="ribbon">
    <svg width="290" height="150" viewBox="0 0 290 150" aria-hidden="true">
      <rect x="175" y="0" width="115" height="44" fill="var(--teal)"/>
      <polygon points="60,48 290,48 290,92 60,92" fill="var(--teal-light)"/>
      <polygon points="40,92 290,92 290,136 40,136 60,114" fill="var(--teal)"/>
      <line x1="175" y1="4" x2="290" y2="4" stroke="#fff" stroke-dasharray="3 3" opacity=".6"/>
      <line x1="60" y1="52" x2="290" y2="52" stroke="#fff" stroke-dasharray="3 3" opacity=".6"/>
      <line x1="50" y1="96" x2="290" y2="96" stroke="#fff" stroke-dasharray="3 3" opacity=".6"/>
    </svg>
    <span class="ribbon__text ribbon__amount">$20</span>
    <span class="ribbon__text ribbon__line1">Gift Card is given</span>
    <span class="ribbon__text ribbon__line2">your first order</span>
  </div>

  <div class="brand"><span class="brand__dot"></span>Linden Medical</div>
  <p class="contact contact--web">www.lindenmedical.com</p>

  <div class="heart-art" role="img" aria-label="Red heart held in a green hand"></div>

  <p class="contact contact--phone">Toll Free Number 55510247</p>
</section>

</body>
</html>
```